Real Estate Company / Capital Needs Cards!

need business cards designed using the logos that were just designed by pixelbarn.

Reason: per designers request deadline extended 1 day…thank you.

Target Market(s)

Investors and clients looking to purchase real estate or invest in the business.

Industry/Entity Type

Business

Requirements
Must have
• two designs - one for the real estate logo and one for the capital logo, similar but slightly different.
Nice to have
• something to make it pop (perhaps on the back)
Should not have
• much color

```html
<!DOCTYPE html>
<html lang="en">
<head>
<meta charset="utf-8">
<title>Norvale Real Estate – Business Cards</title>
<link href="https://fonts.googleapis.com/css2?family=Open+Sans:wght@400;600&display=swap" rel="stylesheet">
<style>
  :root {
    --backdrop: #5a3622;
    --card-black: #050505;
    --silver-light: #f4f4f1;
    --silver-mid: #d2d2cf;
    --silver-dark: #a9a9a6;
    --ink-light: #f2f2f2;
    --brand-silver: #dcdcd8;
  }
  * { margin: 0; padding: 0; box-sizing: border-box; }
  html, body { width: 1200px; height: 434px; overflow: hidden; }
  body {
    background: var(--backdrop);
    font-family: "Open Sans", Arial, sans-serif;
    position: relative;
  }
  .card {
    position: absolute;
    top: 62px;
    width: 530px;
    height: 310px;
    border-radius: 30px;
    overflow: hidden;
  }
  .card-front { left: 50px; }
  .card-back { left: 620px; background: var(--card-black); }
  .card-shape { position: absolute; inset: 0; }

  .brand {
    position: absolute;
    display: flex;
    align-items: center;
    color: var(--brand-silver);
    font-weight: 400;
  }
  .brand-square {
    background: var(--brand-silver);
    flex: none;
  }
  .brand-name { display: flex; flex-direction: column; line-height: 1; }
  .brand-front { left: 92px; top: 130px; gap: 10px; }
  .brand-front .brand-square { width: 38px; height: 38px; border-radius: 4px; }
  .brand-front .brand-main { font-size: 24px; letter-spacing: 1px; }
  .brand-front .brand-sub { font-size: 10px; letter-spacing: 1.6px; margin-top: 4px; }

  .brand-back { left: 90px; top: 108px; gap: 22px; }
  .brand-back .brand-square { width: 92px; height: 92px; border-radius: 10px; }
  .brand-back .brand-main { font-size: 60px; letter-spacing: 3px; }
  .brand-back .brand-sub { font-size: 22px; letter-spacing: 4px; margin-top: 8px; }

  .contact {
    position: absolute;
    left: 318px;
    top: 40px;
    width: 200px;
    color: var(--ink-light);
    font-size: 14px;
    line-height: 1.4;
  }
  .contact-name { font-size: 15px; }
  .contact-title { font-size: 15px; margin-bottom: 20px; }
  .contact-line { display: flex; align-items: center; gap: 4px; margin-bottom: 3px; white-space: nowrap; }
  .contact-email { font-size: 13px; }
  .contact-line svg { width: 12px; height: 12px; flex: none; }
  .contact-address { margin-top: 20px; font-size: 14px; }
</style>
</head>
<body>

<section class="card card-front" aria-label="Business card front">
  <svg class="card-shape" viewBox="0 0 530 310" aria-hidden="true">
    <defs>
      <linearGradient id="silver" x1="0" y1="0" x2="1" y2="1">
        <stop offset="0" stop-color="var(--silver-mid)"/>
        <stop offset="0.45" stop-color="var(--silver-light)"/>
        <stop offset="1" stop-color="var(--silver-dark)"/>
      </linearGradient>
    </defs>
    <rect width="530" height="310" fill="url(#silver)"/>
    <ellipse cx="372" cy="192" rx="338" ry="232" fill="none" stroke="var(--card-black)" stroke-width="2"/>
    <ellipse cx="348" cy="175" rx="326" ry="190" fill="var(--card-black)"/>
    <rect x="300" y="0" width="230" height="310" fill="var(--card-black)"/>
    <line x1="298" y1="22" x2="302" y2="284" stroke="var(--ink-light)" stroke-width="1.5"/>
  </svg>

  <div class="brand brand-front">
    <span class="brand-square"></span>
    <span class="brand-name">
      <span class="brand-main">NORVALE</span>
      <span class="brand-sub">REAL ESTATE</span>
    </span>
  </div>

  <div class="contact">
    <p class="contact-name">Your Name</p>
    <p class="contact-title">Title</p>
    <p class="contact-line">
      <svg viewBox="0 0 12 12"><path d="M3 1l2 2.5-1.2 1.2a6 6 0 0 0 3.5 3.5L8.5 7 11 9l-1.3 1.8C5.5 10.5 1.5 6.5 1.2 2.3z" fill="currentColor"/></svg>
      123-456-7980
    </p>
    <p class="contact-line">
      <svg viewBox="0 0 12 12"><rect x="3" y="1" width="6" height="4" fill="currentColor"/><rect x="1" y="5" width="10" height="6" rx="1" fill="currentColor"/></svg>
      123-568-7896
    </p>
    <p class="contact-line contact-email">
      <svg viewBox="0 0 12 12"><rect x="1" y="3" width="10" height="7" fill="currentColor"/><path d="M1 3l5 4 5-4" fill="none" stroke="#050505" stroke-width="1"/></svg>
      norvaleestate@mail.test
    </p>
    <p class="contact-address">Street Name, City Name<br>State ZipCode</p>
  </div>
</section>

<section class="card card-back" aria-label="Business card back">
  <div class="brand brand-back">
    <span class="brand-square"></span>
    <span class="brand-name">
      <span class="brand-main">NORVALE</span>
      <span class="brand-sub">REAL ESTATE</span>
    </span>
  </div>
</section>

</body>
</html>
```